Business Card Design

New business card design

Target Market(s)

Residential & Commercial Property Managers

Industry/Entity Type

Plumbing Services

Contact Information for Business Card

Name - Rowan Keddle, title - Director, Phone Number - 0431 286 517, email - rowan@tbk-plumbing.com.au, Company ABN - 73 215 904 386,

Font styles to use
Sans Serif

Colors
0054AA
0677BA
7BADD7
CADEEF
E8F1F8

```html
<!DOCTYPE html>
<html lang="en">
<head>
<meta charset="utf-8">
<title>TBK Plumbing Services – Business Card</title>
<link href="https://fonts.googleapis.com/css2?family=Montserrat:wght@400;500;700;800&display=swap" rel="stylesheet">
<style>
  :root {
    --page-bg: #e9ebee;
    --ink-dark: #1d2330;
    --card-dark: #1e2430;
    --accent-blue: #29a9e0;
    --brand-light: #7badd7;
    --card-white: #ffffff;
    --text-dark: #1d2330;
  }
  * { margin: 0; padding: 0; box-sizing: border-box; }
  html, body {
    width: 1200px; height: 931px; overflow: hidden;
    background: var(--page-bg);
    font-family: "Montserrat", sans-serif;
  }
  .stage { position: relative; width: 1200px; height: 931px; }
  .card {
    position: absolute; width: 740px; height: 420px;
    border-radius: 26px; overflow: hidden;
    box-shadow: 0 10px 28px rgba(0,0,0,0.18);
  }
  .card-front { left: 60px; top: 40px; background: var(--card-dark); }
  .card-back { left: 400px; top: 480px; background: var(--card-white); }

  .brand {
    position: absolute; display: flex; align-items: center; gap: 14px;
    font-weight: 500;
  }
  .brand-dot { width: 22px; height: 22px; border-radius: 50%; background: var(--accent-blue); flex: none; }
  .card-front .brand { left: 50%; top: 50%; transform: translate(-50%, -50%); font-size: 40px; color: var(--brand-light); letter-spacing: 1px; white-space: nowrap; }
  .card-back .brand { left: 46px; top: 150px; width: 300px; font-size: 28px; line-height: 1.2; color: var(--text-dark); letter-spacing: 0.5px; }

  .divider { position: absolute; left: 380px; top: 46px; width: 2px; height: 222px; background: var(--ink-dark); }

  .contact { position: absolute; left: 402px; top: 44px; color: var(--text-dark); }
  .contact-name { font-size: 27px; font-weight: 800; line-height: 1.1; }
  .contact-title { font-size: 17px; font-weight: 400; margin: 2px 0 14px 4px; }
  .contact-line { display: flex; align-items: center; gap: 10px; font-size: 16px; margin-bottom: 9px; }
  .contact-line svg { width: 16px; height: 16px; flex: none; fill: var(--ink-dark); }
  .contact-abn { font-size: 16px; margin-top: 4px; }
  .contact-abn strong { font-weight: 800; }

  .band-address {
    position: absolute; left: 0; bottom: 44px; width: 570px; height: 40px;
    background: var(--ink-dark);
    clip-path: polygon(0 0, 100% 0, 97% 100%, 0 100%);
    color: #fff; font-size: 17px; display: flex; align-items: center; padding-left: 120px;
    white-space: nowrap;
  }
  .band-accent {
    position: absolute; right: 0; bottom: 60px; width: 165px; height: 42px;
    background: var(--accent-blue);
    clip-path: polygon(6% 0, 100% 0, 100% 70%, 0 100%);
  }
</style>
</head>
<body>
<main class="stage">
  <section class="card card-front" aria-label="Business card front">
    <div class="brand"><span class="brand-dot"></span>TBK Plumbing Services</div>
  </section>

  <section class="card card-back" aria-label="Business card back">
    <div class="brand"><span class="brand-dot"></span><span>TBK Plumbing Services</span></div>
    <div class="divider"></div>
    <div class="contact">
      <p class="contact-name">Rowan Keddle</p>
      <p class="contact-title">Director</p>
      <p class="contact-line">
        <svg viewBox="0 0 24 24" aria-hidden="true"><path d="M6.6 10.8a15.1 15.1 0 0 0 6.6 6.6l2.2-2.2c.3-.3.7-.4 1-.2 1.1.4 2.3.6 3.6.6.6 0 1 .4 1 1V20c0 .6-.4 1-1 1A17 17 0 0 1 3 4c0-.6.4-1 1-1h3.5c.6 0 1 .4 1 1 0 1.3.2 2.5.6 3.6.1.3 0 .7-.2 1z"/></svg>
        0431 286 517
      </p>
      <p class="contact-line">
        <svg viewBox="0 0 24 24" aria-hidden="true"><path d="M2 5h20v14H2zm2 2v.4l8 5 8-5V7z"/></svg>
        rowan@tbk-plumbing.com.au
      </p>
      <p class="contact-line">
        <svg viewBox="0 0 24 24" aria-hidden="true"><path d="M12 2a10 10 0 1 0 0 20 10 10 0 0 0 0-20zm6.9 6h-3a15 15 0 0 0-1.3-3.9A8 8 0 0 1 18.9 8zM12 4c.8 1.2 1.5 2.5 1.9 4h-3.8c.4-1.5 1.1-2.8 1.900-4zM4.3 14a8 8 0 0 1 0-4h3.4a16 16 0 0 0 0 4zm.8 2h3a15 15 0 0 0 1.3 3.9A8 8 0 0 1 5.1 16zm3-8h-3a8 8 0 0 1 4.3-3.9A15 15 0 0 0 8.1 8zM12 20c-.8-1.2-1.5-2.5-1.9-4h3.8c-.4 1.5-1.1 2.8-1.9 4zm2.3-6H9.7a14 14 0 0 1 0-4h4.6a14 14 0 0 1 0 4zm.3 5.9a15 15 0 0 0 1.3-3.9h3a8 8 0 0 1-4.3 3.9zm1.7-5.9a16 16 0 0 0 0-4h3.4a8 8 0 0 1 0 4z"/></svg>
        www.tbk-plumbing.com.au
      </p>
      <p class="contact-abn"><strong>ABN</strong> - 73 215 904 386</p>
    </div>
    <div class="band-address">48 Harbour Reach Road Kellyville, NSW 2155</div>
    <div class="band-accent"></div>
  </section>
</main>
</body>
</html>
```